Yacht, Boats, Watersports company needs a redesign of business card

Hello Designers!
We are a Boat dealership company that sells fun in the water, we sell boats, Yachts, Kayaks and also yacht WaterSport toys. We are looking to redesign our business cards in to something a little bit more sophisticated. in a way that we can make better use of our company colors. I'm attaching a zipped file containing the company 3 sets of company logo which one is an horizontal another one is a vertical and also a chromed 3d logo. Also is included two set of business cards that we use and also some designs that i think it's interesting. We use PMS 2026c Orange and PMS 7687C Blue. I would like to see at least two different options with the orange as accent and also using blue as an accent color. It's really important for the business cards to have a font option and size that is legible to most people. Our current website is wwww.coralpennant.com. Please visit if you want to have a better feeling of the Boat dealership
You can send Single sided or double side options. We are now using single sided but we may be open for a double side option if we really like the design.
Target Market(s)
Marine, boat sales, yacht sales, water toys sales/
Contact Information for Business Card
Name: Dale Whitcombe
Address: 212 North Fenwick Lane,
Marlow Key, FL 33190
Phone: 954-731-8842
Fax: 954:731-8843
Cell: 954-382-1490
Email: dw@coralpennant.com
Website: coralpennant.com
Requirements
Must have
- the current information of the business card provided.
logo
use the PMS Colors
Nice to have
- a touch of elegance and sophistication but simple
Should not have
- should not have any typography that is hard to read, the card should be simple but yet sophisticated.

```html
<!DOCTYPE html>
<html lang="en">
<head>
<meta charset="utf-8">
<title>Coral Pennant — Business Card</title>
<link href="https://fonts.googleapis.com/css2?family=Michroma&family=Arimo:wght@400;700&display=swap" rel="stylesheet">
<style>
  :root {
    --blue: #0f4a80;
    --orange: #f0612b;
    --ink: #2a2a2a;
    --rule: #d6d6d6;
    --paper: #ffffff;
    --stage: #2f2f2f;
    --faint: #f3f3f3;
  }
  html, body { margin: 0; padding: 0; overflow: hidden; }
  body {
    width: 1200px; height: 866px;
    background: var(--stage);
    font-family: "Arimo", Arial, sans-serif;
    position: relative;
  }
  .card {
    position: absolute;
    top: 284px;
    width: 520px; height: 297px;
    overflow: hidden;
    box-shadow: 0 10px 30px rgba(0,0,0,.45);
  }
  .card--front { left: 50px; background: var(--paper); }
  .card--back { left: 630px; background: var(--blue); }

  .faint-ring {
    position: absolute; left: 40px; top: -30px;
    width: 260px; height: 260px; border-radius: 50%;
    border: 26px solid var(--faint);
  }
  .card--back .faint-ring { left: 150px; top: 10px; border-color: rgba(255,255,255,.04); width: 300px; height: 300px; }

  .brand {
    position: absolute; display: flex; align-items: center; gap: 10px;
    font-family: "Michroma", sans-serif; font-size: 15px; letter-spacing: 1px;
    white-space: nowrap;
  }
  .brand__dot {
    width: 30px; height: 30px; border-radius: 50%;
    border: 4px solid var(--orange); box-sizing: border-box;
  }
  .card--front .brand { left: 230px; top: 46px; color: var(--blue); }
  .card--back .brand { left: 120px; top: 112px; color: #fff; font-size: 17px; }
  .card--back .brand__dot { width: 40px; height: 40px; border-width: 5px; }

  .holder {
    position: absolute; left: 26px; top: 40px;
    font-family: "Michroma", sans-serif; font-size: 13px; letter-spacing: .5px;
    white-space: nowrap;
  }
  .holder__first { color: var(--blue); }
  .holder__last { color: var(--orange); }

  .contacts {
    position: absolute; left: 26px; top: 72px;
    list-style: none; margin: 0; padding: 0;
    font-size: 11.5px; line-height: 16px; color: var(--ink);
  }
  .contacts li { display: flex; align-items: center; gap: 7px; }
  .contacts svg { width: 11px; height: 11px; fill: var(--blue); flex: none; }
  .web-domain { color: var(--orange); }
  .web-prefix, .web-tld { color: var(--blue); }

  .divider {
    position: absolute; left: 230px; right: 30px; top: 150px;
    height: 1px; background: var(--rule);
  }
  .address {
    position: absolute; right: 30px; bottom: 28px; text-align: right;
    font-size: 12.5px; line-height: 17px; color: var(--ink); font-style: normal;
  }

  .card--back .site {
    position: absolute; left: 0; right: 0; top: 178px; text-align: center;
    font-size: 14px; letter-spacing: .5px; color: #fff;
  }
  .card--back .site .web-domain { color: var(--orange); }
</style>
</head>
<body>

<section class="card card--front">
  <div class="faint-ring"></div>

  <div class="brand"><span class="brand__dot"></span>CORAL PENNANT</div>

  <div class="holder"><span class="holder__first">DALE</span> <span class="holder__last">WHITCOMBE</span></div>

  <ul class="contacts">
    <li><svg viewBox="0 0 12 12"><path d="M2 1h3l1 3-2 1a7 7 0 0 0 3 3l1-2 3 1v3c-6 0-9-3-9-9z"/></svg>954-731-8842</li>
    <li><svg viewBox="0 0 12 12"><path d="M3 1h6v3H3zM1 5h10v5H9v1H3v-1H1zM4 8v2h4V8z"/></svg>954:731-8843</li>
    <li><svg viewBox="0 0 12 12"><path d="M3 0h6v12H3zM4 1v8h4V1z"/></svg>954-382-1490</li>
    <li><svg viewBox="0 0 12 12"><path d="M0 2h12v8H0zM1 3l5 4 5-4"/></svg>dw@coralpennant.com</li>
    <li><svg viewBox="0 0 12 12"><circle cx="6" cy="6" r="5.5"/></svg><span><span class="web-prefix">www.</span><span class="web-domain">coralpennant</span><span class="web-tld">.com</span></span></li>
  </ul>

  <div class="divider"></div>

  <address class="address">212 North Fenwick Lane<br>Marlow Key, FL 33190</address>
</section>

<section class="card card--back">
  <div class="faint-ring"></div>
  <div class="brand"><span class="brand__dot"></span>CORAL PENNANT</div>
  <div class="site">www.<span class="web-domain">coralpennant</span>.com</div>
</section>

</body>
</html>
```